IT Company requires new Business Card design.

Over the years we have had a few different business card designs. We are now due for new cards across the board for all staff. We felt this would be a good time to start fresh with a new design. Our traditional card simply had our details on the front, and a list of services on the back. We don't particularly need the list of services, we have had cards where the only thing on the rear of the card was our logo.
Feel free to be creative, we would like our tag line "Full-Service IT Support" to appear at some point, doesn't necessarily have to be with the logo.
I have attached samples and drafts of various previous cards we have used over the years.

```html
<!DOCTYPE html>
<html lang="en">
<head>
<meta charset="utf-8">
<title>Harbour Systems – Business Card</title>
<link rel="stylesheet" href="https://fonts.googleapis.com/css2?family=Open+Sans:wght@400;600;800&display=swap">
<style>
  :root {
    --slate: #5f7382;
    --paper: #ffffff;
    --backdrop: #e4e4ea;
    --ink-light: #ffffff;
    --divider: rgba(255,255,255,0.55);
  }
  * { margin: 0; padding: 0; box-sizing: border-box; }
  html, body {
    width: 1200px; height: 987px; overflow: hidden;
    background: var(--backdrop);
    font-family: "Open Sans", Arial, sans-serif;
  }
  .sheet {
    width: 1200px; height: 987px;
    display: flex; flex-direction: column; align-items: center;
    justify-content: center; gap: 26px;
  }
  .card {
    width: 800px; height: 457px;
    background: var(--paper);
    border-radius: 28px;
    overflow: hidden;
    position: relative;
    box-shadow: 0 2px 10px rgba(0,0,0,0.12);
  }

  /* Front */
  .front .brand {
    position: absolute; left: 150px; top: 44px;
    display: flex; align-items: center; gap: 18px;
  }
  .brand-square {
    width: 58px; height: 58px; background: var(--slate); flex: none;
  }
  .brand-name {
    color: var(--slate); font-weight: 800; font-size: 50px;
    letter-spacing: 1px; line-height: 1; white-space: nowrap;
  }
  .front .band {
    position: absolute; left: 0; right: 0; top: 150px; height: 238px;
    background: var(--slate); color: var(--ink-light);
    display: flex; align-items: center;
  }
  .identity {
    width: 340px; text-align: right; padding-right: 28px;
    font-size: 19px; line-height: 1.45;
  }
  .identity .person { font-weight: 800; font-size: 25px; }
  .divider {
    width: 1px; height: 160px; background: var(--divider);
  }
  .contacts {
    list-style: none; padding-left: 26px;
    font-size: 20px; line-height: 1.5;
  }
  .contacts li { display: flex; align-items: center; gap: 12px; white-space: nowrap; }
  .contacts svg { width: 20px; height: 20px; flex: none; }
  .tagline {
    position: absolute; left: 0; width: 420px; top: 408px;
    text-align: center;
    color: var(--slate); font-size: 19px; letter-spacing: 5px;
    text-transform: uppercase; white-space: nowrap;
  }

  /* Back */
  .back .brand {
    position: absolute; inset: 0 0 70px 0;
    display: flex; align-items: center; justify-content: center; gap: 22px;
  }
  .back .brand-square { width: 80px; height: 80px; }
  .back .brand-name { font-size: 60px; }
  .back .web {
    position: absolute; left: 0; right: 0; bottom: 70px;
    text-align: center; color: var(--slate);
    font-size: 22px; letter-spacing: 2px;
  }
</style>
</head>
<body>
<main class="sheet">

  <section class="card front" aria-label="Business card front">
    <div class="brand">
      <span class="brand-square"></span>
      <span class="brand-name">HARBOUR SYSTEMS</span>
    </div>

    <div class="band">
      <div class="identity">
        <div class="person">Daniel Reeve</div>
        <div>Operation Manager</div>
        <div>Unit 4 18 Marlow Street</div>
        <div>Bibra Lake WA 6163</div>
      </div>
      <div class="divider"></div>
      <ul class="contacts">
        <li>
          <svg viewBox="0 0 20 20" aria-hidden="true"><circle cx="10" cy="10" r="9" fill="none" stroke="#fff" stroke-width="1.6"/><path d="M7 5.5l2 2-1 1.3c.7 1.4 1.8 2.5 3.2 3.2l1.3-1 2 2-1.3 1.5c-3.6-.6-6.7-3.7-7.3-7.3z" fill="#fff"/></svg>
          08 9300 1122
        </li>
        <li>
          <svg viewBox="0 0 20 20" aria-hidden="true"><rect x="6" y="2" width="8" height="16" rx="1.5" fill="none" stroke="#fff" stroke-width="1.6"/><rect x="8" y="4.5" width="4" height="5" fill="#fff"/><circle cx="10" cy="14.5" r="1" fill="#fff"/></svg>
          0400 555 817
        </li>
        <li>
          <svg viewBox="0 0 20 20" aria-hidden="true"><rect x="6" y="2" width="8" height="6" fill="none" stroke="#fff" stroke-width="1.6"/><rect x="2" y="8" width="16" height="9" rx="1.5" fill="#fff"/></svg>
          08 9300 1122
        </li>
        <li>
          <svg viewBox="0 0 20 20" aria-hidden="true"><rect x="2" y="4.5" width="16" height="11" rx="1.5" fill="none" stroke="#fff" stroke-width="1.6"/><path d="M2.5 5l7.5 6 7.5-6" fill="none" stroke="#fff" stroke-width="1.6"/></svg>
          daniel@harboursystems.com.au
        </li>
        <li>
          <svg viewBox="0 0 20 20" aria-hidden="true"><circle cx="10" cy="10" r="8" fill="none" stroke="#fff" stroke-width="1.6"/><ellipse cx="10" cy="10" rx="3.5" ry="8" fill="none" stroke="#fff" stroke-width="1.2"/><path d="M2 10h16" stroke="#fff" stroke-width="1.2"/></svg>
          www.harboursystems.com.au
        </li>
      </ul>
    </div>

    <p class="tagline">Full-Service IT Support</p>
  </section>

  <section class="card back" aria-label="Business card back">
    <div class="brand">
      <span class="brand-square"></span>
      <span class="brand-name">HARBOUR SYSTEMS</span>
    </div>
    <p class="web">www.harboursystems.com.au</p>
  </section>

</main>
</body>
</html>
```